We need a logo for our business which is a dental clinic (i.e. dentistry).
We would lilke designs using the colour blue, green and black incorporating the words Corvath Dental, possibly a smile or a tooth image can be considered for incorporation in the logo.

Industry/Entity Type

Dental

```html
<!DOCTYPE html>
<html lang="en">
<head>
<meta charset="utf-8">
<title>Corvath Dental – Business Card</title>
<link href="https://fonts.googleapis.com/css2?family=Oxygen:wght@400&display=swap" rel="stylesheet">
<style>
  :root {
    --page-bg: #e9ebee;
    --card-blue: #4a78a4;
    --card-mid: #a3bdd3;
    --card-white: #ffffff;
    --ink: #111418;
    --name-blue: #2f5f99;
    --rule: #3a4a5c;
    --mark-blue: #1f4f86;
  }
  * { margin: 0; padding: 0; box-sizing: border-box; }
  html, body {
    width: 1200px; height: 900px; overflow: hidden;
    background: var(--page-bg);
    font-family: "Oxygen", "Helvetica Neue", Arial, sans-serif;
  }
  .business-card {
    position: absolute; left: 100px; top: 164px;
    width: 1000px; height: 572px; overflow: hidden;
    background: linear-gradient(115deg, var(--card-blue) 0%, var(--card-mid) 45%, var(--card-white) 80%);
    box-shadow: 0 6px 18px rgba(0,0,0,0.18);
    color: var(--ink);
  }
  .brand {
    position: absolute; right: 40px; top: 24px;
    display: flex; flex-direction: column; align-items: center; gap: 12px;
  }
  .brand-dot {
    width: 100px; height: 100px; border-radius: 50%;
    background: var(--mark-blue);
  }
  .brand-name {
    font-size: 30px; letter-spacing: 1px; text-transform: uppercase;
    color: var(--ink); white-space: nowrap;
  }
  .holder {
    position: absolute; left: 48px; top: 196px; width: 560px;
  }
  .holder-name {
    font-size: 36px; color: var(--name-blue);
    padding-left: 46px; line-height: 1.1;
  }
  .holder-rule { height: 1px; background: var(--rule); margin-top: 2px; }
  .holder-role { font-size: 24px; padding-left: 46px; margin-top: 4px; }
  .contact-list {
    position: absolute; left: 74px; top: 330px;
    list-style: none; font-size: 28px; line-height: 1.15;
  }
  .contact-item { display: flex; align-items: flex-start; gap: 16px; margin-bottom: 8px; }
  .contact-item:last-child { margin-bottom: 0; }
  .contact-icon { width: 34px; height: 34px; flex: none; margin-top: 1px; }
</style>
</head>
<body>
  <section class="business-card" aria-label="Corvath Dental business card">
    <div class="brand">
      <div class="brand-dot"></div>
      <div class="brand-name">Corvath Dental</div>
    </div>

    <div class="holder">
      <div class="holder-name">Elin Marsh</div>
      <div class="holder-rule"></div>
      <div class="holder-role">Dentist</div>
    </div>

    <ul class="contact-list">
      <li class="contact-item">
        <svg class="contact-icon" viewBox="0 0 24 24" aria-hidden="true"><path d="M12 3 2 12h3v9h5v-6h4v6h5v-9h3z" fill="#111418"/></svg>
        <span>48 Harbor Lane<br>Oregon, USA</span>
      </li>
      <li class="contact-item">
        <svg class="contact-icon" viewBox="0 0 24 24" aria-hidden="true"><circle cx="12" cy="12" r="10" fill="none" stroke="#111418" stroke-width="1.5"/><path d="M8.5 7c-1 1-1 3 1 6s4 4.5 5.5 3.5l1-1-2-2-1 .8c-1-.5-2.3-2-2.7-3l.8-1-2-2.3z" fill="#111418"/></svg>
        <span>555-555-0142</span>
      </li>
      <li class="contact-item">
        <svg class="contact-icon" viewBox="0 0 24 24" aria-hidden="true"><rect x="7" y="2" width="10" height="20" rx="1.5" fill="none" stroke="#111418" stroke-width="1.5"/><rect x="9" y="5" width="6" height="6" fill="none" stroke="#111418"/><path d="M9 14h2M13 14h2M9 17h2M13 17h2" stroke="#111418" stroke-width="1.5"/></svg>
        <span>555-555-0143</span>
      </li>
      <li class="contact-item">
        <svg class="contact-icon" viewBox="0 0 24 24" aria-hidden="true"><circle cx="12" cy="12" r="10" fill="none" stroke="#111418" stroke-width="1.5"/><rect x="6.5" y="8" width="11" height="8" fill="none" stroke="#111418" stroke-width="1.3"/><path d="M6.5 8l5.5 4.5L17.5 8" fill="none" stroke="#111418" stroke-width="1.3"/></svg>
        <span>elinmarsh@example.com</span>
      </li>
    </ul>
  </section>
</body>
</html>
```